Merrowin Vodka logo and label design

We would like a logo and bottle label design for a new line of Ultra-Premium Vodka. The Company is called Merrowin Spirits and is based in Brisbane, Australia. We would like a 'Gatsby/Prohibition era vibe to the design. We want to keep it minimalistic and sleek. We strongly prefer a minimalist design and colour palette. Black,Gold,Grey,White,Silver,Red and Blue

The bottle will be similar in shape to Castellane/Blue Heron. There will also need to be space on the label for required information, as well as short bio of the company, which will be provided to the winning design.
Updates

We would like to add the polish code of arms for Opoczno. Have attached link for reference. https://www.crestarchive-demo.net/crestwiki/index.php?title=Opoczno

Target Market(s)

Luxury brand customers

Logo Text

Merrowin Ultra-Premium Vodka

Logo styles of interest
Wordmark Logo
Lettermark Logo
Requirements
Must have
• This is the first release from our new Vodka label. We want a logo and bottle label that reflects a premium product. We very much like Prohibition/Gatsby era themed bottles and labels. The label and bottle should be elegant and clean.
Should not have
• Anything too busy or confusing.

```html
<!DOCTYPE html>
<html lang="en">
<head>
<meta charset="utf-8">
<title>Merrowin Ultra-Premium Vodka – Label</title>
<link href="https://fonts.googleapis.com/css2?family=Cinzel:wght@500&family=Great+Vibes&family=Montserrat:wght@600&display=swap" rel="stylesheet">
<style>
  :root {
    --brand-blue: #1a6fae;
    --paper: #ffffff;
  }
  * { margin: 0; padding: 0; box-sizing: border-box; }
  html, body {
    width: 1200px;
    height: 960px;
    overflow: hidden;
    background: var(--paper);
  }
  .canvas {
    position: relative;
    width: 1200px;
    height: 960px;
  }
  .label {
    position: absolute;
    left: 392px;
    top: 240px;
    width: 416px;
    height: 480px;
  }
  .label-frame {
    position: absolute;
    inset: 0;
  }
  .antler-crest {
    position: absolute;
    left: 136px;
    top: 38px;
    width: 144px;
    height: 116px;
    background: linear-gradient(180deg, rgba(26,111,174,0.25), rgba(26,111,174,0.55));
    border-radius: 6px;
  }
  .wordmark {
    position: absolute;
    left: 0;
    right: 0;
    top: 168px;
    text-align: center;
    font-family: "Cinzel", serif;
    font-weight: 500;
    font-size: 50px;
    line-height: 1.1;
    letter-spacing: 0;
    color: var(--brand-blue);
  }
  .tier {
    position: absolute;
    left: 93px;
    right: 93px;
    top: 250px;
    height: 24px;
    display: flex;
    align-items: center;
    gap: 10px;
    color: var(--brand-blue);
  }
  .tier-rule {
    flex: 1;
    height: 2px;
    background: var(--brand-blue);
  }
  .tier-name {
    font-family: "Great Vibes", cursive;
    font-size: 22px;
    line-height: 1;
  }
  .product-line {
    position: absolute;
    left: 0;
    right: 0;
    top: 284px;
    text-align: center;
    font-family: "Montserrat", sans-serif;
    font-weight: 600;
    font-size: 16px;
    line-height: 20px;
    letter-spacing: 12px;
    padding-left: 12px;
    color: var(--brand-blue);
  }
  .emblem-dot {
    position: absolute;
    top: 377px;
    width: 12px;
    height: 12px;
    border-radius: 50%;
    background: var(--brand-blue);
  }
  .emblem-dot--left { left: 126px; }
  .emblem-dot--right { left: 278px; }
  .arms-emblem {
    position: absolute;
    left: 164px;
    top: 326px;
    width: 92px;
    height: 116px;
    background: linear-gradient(180deg, rgba(26,111,174,0.45), rgba(26,111,174,0.75));
    border-radius: 4px;
  }
</style>
</head>
<body>
<main class="canvas">
  <section class="label">
    <svg class="label-frame" width="416" height="480" viewBox="0 0 416 480" aria-hidden="true">
      <path d="M3 3 H413 V270 C413 392 320 477 208 477 C96 477 3 392 3 270 Z"
            fill="none" stroke="#1a6fae" stroke-width="5"/>
    </svg>
    <div class="antler-crest" role="img" aria-label="Stylised antler crest illustration"></div>
    <h1 class="wordmark">Merrowin</h1>
    <div class="tier">
      <span class="tier-rule"></span>
      <span class="tier-name">Ultra</span>
      <span class="tier-rule"></span>
    </div>
    <p class="product-line">PREMIUM VODKA</p>
    <span class="emblem-dot emblem-dot--left"></span>
    <div class="arms-emblem" role="img" aria-label="Heraldic emblem"></div>
    <span class="emblem-dot emblem-dot--right"></span>
  </section>
</main>
</body>
</html>
```